Site for entrepreneurs/small businesses needs Logo, Homepage

Looking for a logo, either an icon, or stylized text, or a combination of both, and a home page design which fits with it. The logo will be for use on the public website as well as for printed collateral (business cards, post cards, brochures and various other marketing materials).

The site is called Orbitwell (Orbitwell.example). This is to be a national, and eventually an international brand. The new service will provide an easy-to-use platform for entrepreneurs to build their business and web presence together in an integrated way which allows them to focus on their core competency.

The site/service will be dead-simple to use, A/B/C, 1/2/3. We will want some sort of "Get started for FREE" promotional space to collect the person's email address with multiple points of interest which guide the user back to this one call to action: sign up for free. We will feature editorial/blog stories, customer testimonials, and present several key features the the reader just can't live without if they are starting a new business.

Criteria:
* Refer to our comparable sites/logos in the design document attached
* Incorporate our color scheme (but complementary colors welcome)
* No Serif fonts!
* No photo-realistic elements for logo
* Logo must present well in gray scale and/or black/white (for printed materials)
* Strokes/borders that are wider to promote simplicity (vs. thin/precise lines which promote technical complexity)

Inspirations:
* Creative/Custom (but legible) fonts
* Excitement, energetic, jumping for joy
* Karate / Ninja / Power / Precision
* Dance Moves
* Regional influences: California, Silicon Valley, West Coast, Surf City, Beaches, Sunset
* Simple/easy, no-brainer solutions

Target Market(s)

Small Businesses / Entrepreneurs

Logo Text

Orbitwell or Orbitwell.example

Number of Pages Required

1 page

Font styles to use
Sans Serif
Decorative

Requirements
Must have
• See the attached style guide (PDF)

```html
<!DOCTYPE html>
<html lang="en">
<head>
<meta charset="utf-8">
<title>Orbitwell — Build your business and web presence together</title>
<link rel="stylesheet" href="https://fonts.googleapis.com/css2?family=Lato:wght@400;700;900&family=Open+Sans:ital,wght@0,400;0,600;0,700;1,400&display=swap">
<style>
:root{
  --violet:#6120f1;
  --orange:#f7891c;
  --orange-deep:#f07d10;
  --ink:#1c1c24;
  --navy:#1d2b57;
  --muted:#6d6d78;
  --line:#dedee4;
  --paper:#ffffff;
  --mist:#f1f1f3;
  --footer:#2b0b60;
  --footer-panel:#3a0d85;
  --ghost:#ececef;
}
*{box-sizing:border-box;margin:0;padding:0}
html,body{width:1200px;height:3651px;overflow:hidden}
body{position:relative;background:var(--paper);font-family:"Open Sans",Arial,sans-serif;color:var(--ink)}
.abs{position:absolute}
.heading{font-family:"Lato",Arial,sans-serif;font-weight:900;text-transform:uppercase;text-align:center;left:0;width:1200px;color:var(--ink);font-size:36px;letter-spacing:.5px}
.ghost{font-family:"Lato",Arial,sans-serif;font-weight:900;text-transform:uppercase;text-align:center;left:0;width:1200px;color:var(--ghost);font-size:74px;letter-spacing:1px;line-height:1}
.intro{left:260px;width:680px;text-align:center;font-size:13px;line-height:25px;color:var(--muted)}
.btn{display:flex;align-items:center;justify-content:center;gap:6px;font-family:"Lato",Arial,sans-serif;font-weight:700;font-size:13px;text-transform:uppercase;color:#fff;border-radius:30px}
.btn-arrow{width:12px;height:12px;border-radius:50%;background:#fff;display:inline-flex;align-items:center;justify-content:center}

/* hero */
.hero{left:0;top:0;width:1200px;height:613px;background:var(--violet)}
.brand{display:flex;align-items:center;gap:14px;font-family:"Lato",Arial,sans-serif;font-weight:700;color:#fff;text-transform:uppercase}
.brand-dot{border:7px solid #fff;border-radius:50%}
.nav{top:55px;left:533px;display:flex;gap:26px;font-family:"Lato",Arial,sans-serif;font-weight:700;font-size:14px;color:#fff}
.lang{left:1054px;top:42px;width:48px;height:48px;border-radius:50%;background:var(--orange);color:#fff;font-family:"Lato",Arial,sans-serif;font-weight:700;font-size:14px;display:flex;align-items:center;justify-content:center}
.hero-title{left:97px;top:222px;font-family:"Lato",Arial,sans-serif;font-weight:900;font-size:66px;color:#fff;letter-spacing:1px}
.hero-sub{left:100px;top:322px;width:440px;font-size:18px;line-height:30px;font-weight:600;color:#fff}
.hero-btn{left:100px;top:414px;width:172px;height:44px;border:2px solid #fff}
.hero-art{left:560px;top:243px;width:511px;height:317px;border-radius:40px;background:radial-gradient(ellipse at 45% 50%,#7d4bf7 0%,#6a2cf3 60%,var(--violet) 100%)}

/* what we do */
.platform-art{left:97px;top:893px;width:421px;height:307px;border-radius:50%;background:linear-gradient(140deg,#2c6cd6,#1947a8)}
.platform-title{left:591px;top:903px;font-family:"Lato",Arial,sans-serif;font-weight:700;font-size:28px;color:var(--navy)}
.platform-copy{left:594px;top:972px;width:510px;font-size:12px;line-height:26px;color:var(--muted)}
.read-btn{left:594px;top:1134px;width:156px;height:42px;background:var(--orange)}

/* features */
.features{left:0;top:1310px;width:1200px;height:800px;background:linear-gradient(180deg,#f4f4f6,#ebebee)}
.card{width:304px;height:217px;background:rgba(255,255,255,.82);border:1px solid var(--line);text-align:center}
.card-icon{position:absolute;left:117px;top:24px;width:70px;height:70px;border-radius:18px;background:linear-gradient(135deg,#f8a13a,#2a64c9)}
.card-title{position:absolute;left:0;top:106px;width:100%;font-family:"Lato",Arial,sans-serif;font-weight:700;font-size:19px;color:var(--ink)}
.card-text{position:absolute;left:30px;top:144px;width:244px;font-size:12px;line-height:24px;color:var(--muted)}

/* testimonials */
.testimonials{left:0;top:2105px;width:1200px;height:512px;background:linear-gradient(180deg,var(--orange),var(--orange-deep));clip-path:polygon(0 0,100% 14%,100% 100%,0 88%)}
.avatar{width:117px;height:121px;border-radius:50%;border:5px solid #fff;background:linear-gradient(160deg,#d9b79c,#8b6a55)}
.quote-badge{width:32px;height:32px;border-radius:50%;background:var(--footer);color:#fff;font-family:"Lato",Arial,sans-serif;font-weight:900;font-size:26px;line-height:40px;text-align:center}
.quote{width:340px;font-size:12px;line-height:21px;font-style:italic;font-weight:600;color:#fff}
.client{font-family:"Lato",Arial,sans-serif;font-size:14px;color:#fff;font-weight:900;text-transform:uppercase}
.client span{text-transform:none;font-weight:400;font-size:11px}
.arrow{width:28px;height:28px;border-radius:50%;background:rgba(0,0,0,.35);display:flex;align-items:center;justify-content:center}

/* blog */
.post{width:309px;height:314px;background:#fff;border:1px solid var(--line)}
.post-title{position:absolute;left:24px;top:26px;width:270px;font-family:"Lato",Arial,sans-serif;font-weight:700;font-size:19px;line-height:28px;color:var(--ink)}
.post-meta{position:absolute;left:26px;top:94px;width:260px;display:flex;justify-content:space-between;font-size:11px;color:var(--muted)}
.post-meta span{display:flex;align-items:center;gap:7px}
.post-img{position:absolute;left:0;bottom:0;width:100%;height:180px}
.post-text{position:absolute;left:24px;top:134px;width:262px;font-size:12px;line-height:21px;color:var(--muted)}
.post-btn{left:24px;top:256px;width:124px;height:34px;background:var(--orange);font-size:11px}

/* footer */
.footer{left:0;top:3242px;width:1200px;height:409px;background:var(--footer)}
.signup{left:582px;top:3196px;width:618px;height:360px;background:var(--footer-panel)}
.foot-copy{left:100px;top:3366px;width:400px;font-size:12px;line-height:20px;color:#fff}
.social{top:3480px;width:36px;height:36px;border-radius:50%;border:2px solid #fff}
.field{border:1.5px solid #d8cff2;color:#fff;font-size:13px;padding:8px 12px}
.form-title{left:638px;top:3254px;font-family:"Lato",Arial,sans-serif;font-weight:700;font-size:19px;color:#fff}
.signup-btn{left:947px;top:3466px;width:153px;height:34px;background:var(--orange);font-size:12px}
.divider{left:0;top:3559px;width:1200px;height:1px;background:rgba(255,255,255,.15)}
.copyright{left:0;top:3596px;width:1200px;text-align:center;font-size:12px;color:#fff}
</style>
</head>
<body>

<!-- hero -->
<section class="abs hero">
  <div class="abs brand" style="left:97px;top:42px;font-size:30px">
    <span class="brand-dot" style="width:48px;height:48px"></span>Orbitwell
  </div>
  <nav class="abs nav">
    <span>HOME</span><span>ABOUT US ▾</span><span>SERVICES</span><span>BLOG</span><span>NEWS</span><span>CONTACT</span>
  </nav>
  <div class="abs lang">EN</div>
  <h1 class="abs hero-title">ORBITWELL</h1>
  <p class="abs hero-sub">At vero eos et accusamus iusto dignissimos ducimus qui blanditiis praesentium voluptatum</p>
  <div class="abs btn hero-btn">Get started <span class="btn-arrow"><svg width="6" height="7" viewBox="0 0 6 7"><path d="M1 0l5 3.5L1 7z" fill="#6120f1"/></svg></span></div>
  <div class="abs hero-art" role="img" aria-label="Illustration of a team promoting a business with a megaphone and digital marketing icons"></div>
</section>

<!-- what we do -->
<div class="abs ghost" style="top:705px">What we do</div>
<h2 class="abs heading" style="top:716px">What we do</h2>
<p class="abs intro" style="top:784px">At vero eos et accusamus et iusto odio dignissimos ducimus qui blanditiis praesentium voluptatum deleniti atque corrupti quos dolores et quas molestias excepturi sint occaecati cupiditate non provident similique</p>
<div class="abs platform-art" role="img" aria-label="Illustration of people working with dashboards on a large screen"></div>
<h3 class="abs platform-title">Easy-to-Use Platform</h3>
<p class="abs platform-copy">At vero eos et accusamus et iusto odio dignissimos ducimus qui blanditiis praesentium voluptatum deleniti atque corrupti quos dolores. et quas molestias excepturi sint occaecati cupiditate non provident, similique sunt in culpa qui officia deserunt mollitia animi, id est laborum et dolorum fuga. Et harum quidem rerum facilis est et expedita distinctio. Nam libero tempore, cum soluta nobis est eligendi</p>
<div class="abs btn read-btn">Read more <span class="btn-arrow"><svg width="6" height="7" viewBox="0 0 6 7"><path d="M1 0l5 3.5L1 7z" fill="#f7891c"/></svg></span></div>

<!-- features -->
<section class="abs features" role="img" aria-label="Soft background of a laptop on a desk"></section>
<div class="abs ghost" style="top:1385px;color:#dcdce0">Our key features</div>
<h2 class="abs heading" style="top:1397px">Our key features</h2>
<p class="abs intro" style="top:1463px">At vero eos et accusamus et iusto odio dignissimos ducimus qui blanditiis praesentium voluptatum deleniti atque corrupti quos dolores et quas molestias excepturi sint occaecati cupiditate non provident similique</p>

<div class="abs card" style="left:100px;top:1548px"><div class="card-icon" role="img" aria-label="Icon of a gear held by hands"></div><div class="card-title">Quick Setup</div><div class="card-text">At vero eos et accusamus et iusto odio dignissimos ducimus qui blanditiis</div></div>
<div class="abs card" style="left:448px;top:1548px"><div class="card-icon" role="img" aria-label="Icon of a consultant with a speech bubble"></div><div class="card-title">Consulting Services</div><div class="card-text">At vero eos et accusamus et iusto odio dignissimos ducimus qui blanditiis</div></div>
<div class="abs card" style="left:796px;top:1548px"><div class="card-icon" role="img" aria-label="Icon of rising bars with a dollar sign"></div><div class="card-title">Increasd Demand</div><div class="card-text">At vero eos et accusamus et iusto odio dignissimos ducimus qui blanditiis</div></div>
<div class="abs card" style="left:100px;top:1804px"><div class="card-icon" role="img" aria-label="Icon of a target with an arrow"></div><div class="card-title">High Efficiency</div><div class="card-text">At vero eos et accusamus et iusto odio dignissimos ducimus qui blanditiis</div></div>
<div class="abs card" style="left:448px;top:1804px"><div class="card-icon" role="img" aria-label="Icon of a monitor with a growth chart"></div><div class="card-title">Advanced Analytics</div><div class="card-text">At vero eos et accusamus et iusto odio dignissimos ducimus qui blanditiis</div></div>
<div class="abs card" style="left:796px;top:1804px"><div class="card-icon" role="img" aria-label="Icon of a lightbulb above a bar chart"></div><div class="card-title">High Profitability</div><div class="card-text">At vero eos et accusamus et iusto odio dignissimos ducimus qui blanditiis</div></div>

<!-- testimonials -->
<section class="abs testimonials"></section>
<div class="abs ghost" style="top:2218px;color:rgba(120,50,0,.22)">Testimonials</div>
<h2 class="abs heading" style="top:2230px;color:#fff">What our clients say</h2>
<div class="abs arrow" style="left:15px;top:2396px"><svg width="10" height="10" viewBox="0 0 10 10"><path d="M7 1L3 5l4 4" stroke="#fff" stroke-width="2" fill="none"/></svg></div>
<div class="abs arrow" style="left:1157px;top:2396px"><svg width="10" height="10" viewBox="0 0 10 10"><path d="M3 1l4 4-4 4" stroke="#fff" stroke-width="2" fill="none"/></svg></div>

<div class="abs avatar" style="left:102px;top:2342px" role="img" aria-label="Portrait of client Mira Castell"></div>
<div class="abs quote-badge" style="left:145px;top:2447px">”</div>
<p class="abs quote" style="left:243px;top:2354px">“ Magni dolores eos qui ratne voluptem sequi nesciunt Nam libero tempore, cum soluta nobis est eligendi quod maxime placeat facere possimus.”</p>
<div class="abs client" style="left:243px;top:2438px">Mira Castell, <span>Harbor Lane</span></div>

<div class="abs avatar" style="left:645px;top:2342px;background:linear-gradient(160deg,#c9a58a,#6d5141)" role="img" aria-label="Portrait of client Owen Barlow"></div>
<div class="abs quote-badge" style="left:688px;top:2447px">”</div>
<p class="abs quote" style="left:786px;top:2354px">“ Magni dolores eos qui ratne voluptem sequi nesciunt Nam libero tempore, cum soluta nobis est eligendi quod maxime placeat facere possimus.”</p>
<div class="abs client" style="left:786px;top:2438px">Owen Barlow, <span>Joyal Cordinator</span></div>

<!-- blog -->
<div class="abs ghost" style="top:2680px">Latest blog</div>
<h2 class="abs heading" style="top:2692px">Latest blog</h2>

<article class="abs post" style="left:100px;top:2782px">
  <h3 class="post-title">Excepteur sint occaecat sunt cupidatat non proident.</h3>
  <div class="post-meta">
    <span><svg width="11" height="11" viewBox="0 0 11 11"><circle cx="5.5" cy="3" r="2.6" fill="#1d2b57"/><path d="M0.5 11c0-3 2.2-4.6 5-4.6s5 1.6 5 4.6z" fill="#1d2b57"/></svg>Dana Whitlow</span>
    <span><svg width="11" height="11" viewBox="0 0 11 11"><rect x="0.5" y="1.5" width="10" height="9" fill="none" stroke="#1d2b57"/><rect x="0.5" y="1.5" width="10" height="3" fill="#1d2b57"/></svg>May 30, 2018</span>
  </div>
  <div class="post-img" style="background:linear-gradient(135deg,#31a3db,#1b7cc1)" role="img" aria-label="Illustration of a team presenting charts"></div>
</article>

<article class="abs post" style="left:445px;top:2782px">
  <h3 class="post-title">Nemo enim ipsam voluptatem quia voluptas sit odit</h3>
  <div class="post-meta">
    <span><svg width="11" height="11" viewBox="0 0 11 11"><circle cx="5.5" cy="3" r="2.6" fill="#1d2b57"/><path d="M0.5 11c0-3 2.2-4.6 5-4.6s5 1.6 5 4.6z" fill="#1d2b57"/></svg>Dana Whitlow</span>
    <span><svg width="11" height="11" viewBox="0 0 11 11"><rect x="0.5" y="1.5" width="10" height="9" fill="none" stroke="#1d2b57"/><rect x="0.5" y="1.5" width="10" height="3" fill="#1d2b57"/></svg>May 30, 2018</span>
  </div>
  <p class="post-text">Nam libero tempore, cum soluta nobis est eligendi optio cumque nihil impedit quo minus id quod ma xime placeat fafsers cere possimus sed quia non numquam....</p>
  <div class="abs btn post-btn">Read more <span class="btn-arrow"><svg width="6" height="7" viewBox="0 0 6 7"><path d="M1 0l5 3.5L1 7z" fill="#f7891c"/></svg></span></div>
</article>

<article class="abs post" style="left:791px;top:2782px">
  <h3 class="post-title">Sed quia non numquam eius modi tempora incidunt</h3>
  <div class="post-meta">
    <span><svg width="11" height="11" viewBox="0 0 11 11"><circle cx="5.5" cy="3" r="2.6" fill="#1d2b57"/><path d="M0.5 11c0-3 2.2-4.6 5-4.6s5 1.6 5 4.6z" fill="#1d2b57"/></svg>Dana Whitlow</span>
    <span><svg width="11" height="11" viewBox="0 0 11 11"><rect x="0.5" y="1.5" width="10" height="9" fill="none" stroke="#1d2b57"/><rect x="0.5" y="1.5" width="10" height="3" fill="#1d2b57"/></svg>May 30, 2018</span>
  </div>
  <div class="post-img" style="background:linear-gradient(135deg,#2fc48f,#17a673)" role="img" aria-label="Illustration of a calculator, magnifier and documents on a desk"></div>
</article>

<!-- footer -->
<footer class="abs footer"></footer>
<div class="abs brand" style="left:100px;top:3296px;font-size:24px">
  <span class="brand-dot" style="width:40px;height:40px;border-width:6px"></span>Orbitwell
</div>
<p class="abs foot-copy">At vero eos et accusamus et iusto odio dignissimos ducimus qui blanditiis praesentium voluptatum deleniti atque corrupti quos dolores et quas molestias excepturi sint occaecati cupiditate non provident, similique sunt in culpa qui officia deserunt</p>
<div class="abs social" style="left:98px" aria-label="Social profile"></div>
<div class="abs social" style="left:144px;background:#2a8fe6;border-color:#2a8fe6" aria-label="Social profile"></div>
<div class="abs social" style="left:190px" aria-label="Social profile"></div>
<div class="abs social" style="left:236px" aria-label="Social profile"></div>

<section class="abs signup">
</section>
<h3 class="abs form-title">GET STARTED FOR FREE</h3>
<div class="abs field" style="left:638px;top:3313px;width:221px;height:37px">Name</div>
<div class="abs field" style="left:881px;top:3313px;width:219px;height:37px">Email</div>
<div class="abs field" style="left:638px;top:3364px;width:462px;height:78px">Message</div>
<div class="abs btn signup-btn">Sign up for free</div>

<div class="abs divider"></div>
<p class="abs copyright">Copyright © 2018 Orbitwell. All Rights Reserved.</p>

</body>
</html>
```